Business Card for Industrial Distributor

We need a business card design for an industrial distributor. We sell machine parts for the manufacturing and oil industry. We would like the cards to look clean and modern but with a touch of industry.

Our colors are blue/white.

Please feel free to visit our website www.korvelpartsco.com

Target Market(s)

mexican manufacturers in the automobile/aerospace industry

Industry/Entity Type

Industrial

Colors
ffffff
0555a3

```html
<!DOCTYPE html>
<html lang="en">
<head>
<meta charset="utf-8">
<title>Korvel Business Card</title>
<link rel="stylesheet" href="https://fonts.googleapis.com/css2?family=Roboto:wght@400;700&display=swap">
<style>
  :root {
    --backdrop: #3b3531;
    --card: #141414;
    --card-edge: #1d1d1d;
    --blue: #3a4fc4;
    --blue-deep: #0555a3;
    --white: #ffffff;
    --muted: #b9b9b9;
    --rule: #6d6d6d;
    --mark: #262626;
  }
  * { margin: 0; padding: 0; box-sizing: border-box; }
  html, body { width: 1200px; height: 864px; overflow: hidden; }
  body {
    background: var(--backdrop);
    font-family: "Roboto", Arial, sans-serif;
    position: relative;
  }
  .card {
    position: absolute;
    width: 520px;
    height: 297px;
    background: var(--card);
    border: 1px solid var(--card-edge);
    box-shadow: 0 18px 40px rgba(0,0,0,.45);
  }
  /* back face */
  .card-back { left: 70px; top: 150px; }
  .card-back .mark {
    position: absolute;
    left: 190px; top: 55px;
    width: 140px; height: 140px;
    border-radius: 50%;
    background: var(--mark);
  }
  .card-back .web {
    position: absolute;
    left: 0; right: 0; top: 232px;
    text-align: center;
    color: var(--muted);
    font-size: 12px;
    letter-spacing: 5px;
  }
  /* front face */
  .card-front { left: 610px; top: 420px; color: var(--white); }
  .brand {
    position: absolute;
    right: 34px; top: 40px;
    display: flex; align-items: center; gap: 8px;
  }
  .brand-dot {
    width: 30px; height: 30px; border-radius: 50%;
    background: var(--blue);
  }
  .brand-name {
    color: var(--blue);
    font-size: 36px; font-weight: 700;
    letter-spacing: -0.5px;
  }
  .person { position: absolute; left: 32px; top: 68px; }
  .person-name {
    color: var(--blue);
    font-size: 17px;
    text-transform: uppercase;
    line-height: 1.1;
  }
  .person-role { font-size: 15px; line-height: 1.2; }
  .divider {
    position: absolute;
    left: 100px; right: 28px; top: 106px;
    height: 1px; background: var(--rule);
  }
  .contacts {
    position: absolute; left: 32px; top: 118px;
    list-style: none; font-size: 13.5px;
  }
  .contacts li { display: flex; align-items: center; gap: 9px; height: 20px; }
  .contacts svg { width: 12px; height: 12px; fill: var(--blue); flex: none; }
  .address {
    position: absolute; left: 330px; top: 214px;
    font-size: 14px; line-height: 1.45;
  }
</style>
</head>
<body>
  <section class="card card-back">
    <div class="mark"></div>
    <p class="web">www.korvelpartsco.com</p>
  </section>

  <section class="card card-front">
    <div class="brand">
      <span class="brand-dot"></span>
      <span class="brand-name">Korvel</span>
    </div>

    <div class="person">
      <p class="person-name">Mark Elden</p>
      <p class="person-role">President</p>
    </div>
    <div class="divider"></div>

    <ul class="contacts">
      <li>
        <svg viewBox="0 0 12 12"><path d="M1 4c0-2 2-3 5-3s5 1 5 3l-2 1-1-2H4L3 5 1 4zM2 6h8l1 5H1z"/></svg>
        (555) 214 - 3080
      </li>
      <li>
        <svg viewBox="0 0 12 12"><path d="M3 1h6v3H3zM1 5h10v5H9V8H3v2H1zM3 9h6v2H3z"/></svg>
        (555) 214 - 3086
      </li>
      <li>
        <svg viewBox="0 0 12 12"><path d="M0 2h12v1L6 7 0 3zM0 4.5l6 4 6-4V10H0z"/></svg>
        sales@korvelpartsco.com
      </li>
      <li>
        <svg viewBox="0 0 12 12"><circle cx="6" cy="6" r="5.5"/><path d="M1 6h10M6 .5c-2 3-2 8 0 11M6 .5c2 3 2 8 0 11" stroke="#141414" stroke-width="0.9" fill="none"/></svg>
        www.korvelpartsco.com
      </li>
    </ul>

    <address class="address" style="font-style:normal">
      Korvel International Corp<br>
      2740 Harbor Mill Rd<br>
      Lanford.TX 75410
    </address>
  </section>
</body>
</html>
```